Haulage company, lets use ruby red white and some 3rd color for web design. and Garvel Pryce Transport logo

Target Market(s)

Transport industry

Industry/Entity Type

transport

Number of Pages Required

2 page

Requirements
Must have
• Logo

```html
<!DOCTYPE html>
<html lang="en">
<head>
<meta charset="utf-8">
<title>Garvel Pryce Transport</title>
<link href="https://fonts.googleapis.com/css2?family=Montserrat:wght@400;500;600;700;800&display=swap" rel="stylesheet">
<style>
:root{
  --ruby:#9d1823;
  --ruby-dark:#7d121b;
  --ruby-soft:#b8303a;
  --gold:#e0aa3e;
  --gold-light:#efc86d;
  --ink:#1b1b1b;
  --grey:#5a5a5a;
  --white:#ffffff;
  --black:#0d0d0d;
}
*{margin:0;padding:0;box-sizing:border-box}
html,body{width:1200px;height:4481px;overflow:hidden}
body{position:relative;font-family:"Montserrat",sans-serif;color:var(--ink);background:var(--white)}
.abs{position:absolute}
.btn{position:absolute;display:flex;align-items:center;justify-content:center;border-radius:30px;font-weight:700;font-size:14px;letter-spacing:.3px;text-transform:uppercase}
.btn-ruby{background:var(--ruby);color:var(--white)}
.btn-gold{background:var(--gold-light);color:var(--ruby)}
.photo{position:absolute}

/* header */
.topline{position:absolute;left:0;top:0;width:1200px;height:4px;background:var(--gold)}
.header{position:absolute;left:0;top:4px;width:1200px;height:121px;background:#fafafa}
.logo{position:absolute;left:110px;top:20px;font-weight:800;font-size:35px;line-height:46px;color:var(--ruby);text-transform:uppercase}
.contact-item{position:absolute;top:22px;display:flex;align-items:center;gap:10px;font-size:14px;color:var(--ruby)}
.icon-circle{width:30px;height:30px;border:2px solid var(--ruby);border-radius:50%;display:flex;align-items:center;justify-content:center}
.nav{position:absolute;left:0;top:71px;width:1200px;height:54px}
.nav ul{position:absolute;top:0;left:0;list-style:none}
.nav li{position:absolute;top:17px;font-size:15px;color:var(--white);white-space:nowrap}

/* hero */
.hero-photo{left:0;top:125px;width:1200px;height:557px;background:linear-gradient(90deg,#f1f1f0 0%,#e7e7e6 35%,#b9bcbd 55%,#8a8f8f 75%,#6e7466 100%)}
.hero-photo::after{content:"";position:absolute;left:0;top:0;width:60%;height:100%;background:linear-gradient(90deg,rgba(255,255,255,.85),rgba(255,255,255,0))}
.hero-kicker{position:absolute;left:110px;top:236px;font-size:30px;font-weight:800;color:var(--ink)}
.hero-title{position:absolute;left:108px;top:274px;font-size:51px;line-height:60px;font-weight:800;text-transform:uppercase}
.hero-title .l1{color:var(--ruby);display:block}
.hero-title .l2{color:var(--gold);display:block}
.hero-text{position:absolute;left:110px;top:410px;width:470px;font-size:15px;line-height:31px;color:#3a3a3a}

/* about */
.about-frame{position:absolute;left:110px;top:790px;width:438px;height:372px;border:3px solid var(--gold)}
.about-photo{left:141px;top:816px;width:438px;height:374px;background:linear-gradient(180deg,#b8c2c8 0%,#dfe3e5 40%,#a9a9a6 75%,#6d6d6b 100%)}
.section-title{font-weight:800;font-size:38px;color:var(--ruby);text-transform:uppercase}
.about-title{position:absolute;left:627px;top:795px}
.about-text{position:absolute;left:628px;top:860px;width:410px;font-size:15.5px;line-height:30px;color:#4a4a4a}

/* services */
.services{position:absolute;left:0;top:1301px;width:1200px;height:631px;background:linear-gradient(120deg,var(--ruby-soft) 0%,var(--ruby) 45%,var(--ruby-dark) 100%)}
.services-title{position:absolute;left:107px;top:1415px;font-size:38px;line-height:52px;font-weight:800;color:var(--white)}
.services-text{position:absolute;left:106px;top:1534px;width:320px;font-size:15px;line-height:29px;color:var(--white)}
.card{position:absolute;background:var(--white);border-radius:6px;box-shadow:0 3px 12px rgba(0,0,0,.15)}
.card .img{position:absolute;left:7px;top:6px;right:7px;border-radius:4px}
.card h3{position:absolute;left:18px;font-weight:600;font-size:22px;color:var(--ink)}
.card p{position:absolute;left:18px;right:14px;font-size:13.5px;line-height:28px;color:#444}
.card .more{position:absolute;left:22px;font-size:14.5px;font-weight:700;color:var(--ruby);display:flex;align-items:center;gap:6px}
.dot{position:absolute;top:1829px;height:5px;border-radius:3px;background:var(--white)}

/* blog */
.blog-title{position:absolute;left:0;top:2022px;width:1200px;text-align:center}
.blog-card h3{font-size:21px;line-height:30px;font-weight:700;left:20px;right:16px}
.date{position:absolute;left:22px;display:flex;align-items:center;gap:8px;font-size:13px;font-weight:600;color:var(--ink)}

/* contact */
.contact-photo{left:600px;top:2699px;width:600px;height:722px;background:linear-gradient(180deg,#ecedee 0%,#d7dde2 45%,#8c9ab0 80%,#5f6c82 100%)}
.contact-panel{position:absolute;left:0;top:2699px}
.contact-title{position:absolute;left:110px;top:2800px;font-weight:800;font-size:38px;color:var(--white)}
.label{position:absolute;font-size:14px;font-weight:500;color:var(--white)}
.field{position:absolute;height:51px;border-radius:26px;background:var(--ruby-dark);border:1px solid rgba(255,255,255,.15);display:flex;align-items:center;justify-content:flex-end;padding-right:18px}

/* why */
.why-title{position:absolute;left:0;top:3510px;width:1200px;text-align:center}
.why-item{position:absolute;width:240px;text-align:center}
.why-item h4{font-size:21px;line-height:35px;font-weight:600;color:var(--ink)}
.why-item p{font-size:14px;line-height:29px;color:#555;margin-top:8px}
.why-icon{position:absolute;width:148px;height:148px;border-radius:50%;background:rgba(157,24,35,.15);display:flex;align-items:center;justify-content:center}
.why-icon span{width:132px;height:132px;border-radius:50%;background:var(--ruby);display:flex;align-items:center;justify-content:center}

/* footer */
.footer{position:absolute;left:0;top:4061px;width:1200px;height:420px;background:var(--black);color:var(--white)}
.footer-logo{position:absolute;left:110px;top:97px;font-size:29px;line-height:40px;font-weight:800;color:var(--ruby);text-transform:uppercase}
.social{position:absolute;top:232px;width:34px;height:34px;border-radius:50%;background:var(--white)}
.footer h5{position:absolute;top:93px;font-size:21px;font-weight:600}
.footer ul{position:absolute;list-style:none;top:146px;font-size:14px;line-height:28.5px}
.footer ul li{display:flex;align-items:center;gap:8px}
.subscribe{position:absolute;left:889px;top:90px;width:196px;height:238px;background:var(--ruby);border-radius:6px;text-align:center}
.subscribe h6{margin-top:32px;font-size:22px;font-weight:700;color:var(--gold)}
.subscribe p{margin:10px auto 0;width:170px;font-size:12.5px;line-height:28px}
.sub-input{position:absolute;left:19px;top:168px;width:164px;height:36px;border:1px solid var(--white);border-radius:18px;font-size:10.5px;display:flex;align-items:center;padding-left:10px}
.sub-go{position:absolute;right:3px;top:3px;width:28px;height:28px;border-radius:50%;background:var(--gold-light);display:flex;align-items:center;justify-content:center}
.footer-rule{position:absolute;left:106px;top:363px;width:979px;height:1px;background:#bdbdbd}
.copyright{position:absolute;left:0;top:381px;width:1200px;text-align:center;font-size:13px}
</style>
</head>
<body>

<!-- header -->
<div class="header">
  <div class="logo">Garvel Pryce<br>Transport</div>
  <div class="contact-item" style="left:419px">
    <span class="icon-circle"><svg width="14" height="11" viewBox="0 0 14 11"><rect x="1" y="1" width="12" height="9" fill="none" stroke="#9d1823" stroke-width="1.5"/><path d="M1 1l6 5 6-5" fill="none" stroke="#9d1823" stroke-width="1.5"/></svg></span>
    info@garvelpryce.com
  </div>
  <div class="contact-item" style="left:696px">
    <span class="icon-circle"><svg width="14" height="14" viewBox="0 0 24 24"><path d="M6.6 10.8a15 15 0 006.6 6.6l2.2-2.2a1 1 0 011-.25 11.4 11.4 0 003.6.6 1 1 0 011 1V20a1 1 0 01-1 1A17 17 0 013 4a1 1 0 011-1h3.5a1 1 0 011 1c0 1.25.2 2.45.6 3.6a1 1 0 01-.25 1z" fill="#9d1823"/></svg></span>
    +1 555 010 2040
  </div>
  <div class="btn btn-ruby" style="left:913px;top:10px;width:172px;height:45px;font-size:15px;color:var(--gold-light)">Get in touch</div>
</div>
<div class="topline"></div>
<nav class="nav">
  <svg class="abs" style="left:0;top:0" width="1200" height="54"><polygon points="412,0 1200,0 1200,54 395,54" fill="#9d1823"/></svg>
  <ul>
    <li style="left:454px">HOME</li>
    <li style="left:551px">ABOUT US</li>
    <li style="left:682px">SERVICES</li>
    <li style="left:808px">TESTIMONIALS</li>
    <li style="left:971px">CONTACT US</li>
  </ul>
</nav>

<!-- hero -->
<div class="photo hero-photo" role="img" aria-label="White and red articulated truck parked on a concrete yard beside green fields"></div>
<div class="hero-kicker">WELCOME TO</div>
<h1 class="hero-title"><span class="l1">Garvel Pryce</span><span class="l2">Transport</span></h1>
<p class="hero-text">Lorem Ipsum is simply dummy text of the printing and typesetting industry. Lorem Ipsum has been the industry's</p>
<div class="btn btn-ruby" style="left:110px;top:492px;width:172px;height:47px;color:var(--gold-light)">Get started</div>

<!-- about -->
<div class="about-frame"></div>
<div class="photo about-photo" role="img" aria-label="Red and white truck with a white trailer on a wet yard"></div>
<h2 class="section-title about-title">About us</h2>
<p class="about-text">Lorem Ipsum is simply dummy text of the printing and typesetting industry. Lorem Ipsum has been the industry's standard dummy text ever since the 1500s, when an unknown printer took a galley of type and scrambled it to make a type specimen book. It has survived not only five centuries, but also the leap into electronic typesetting, remaining essentially unchanged.</p>
<div class="btn btn-ruby" style="left:630px;top:1127px;width:172px;height:47px">Read more</div>

<!-- services -->
<section class="services"></section>
<h2 class="services-title">EXPLORE OUR<br>SERVICES</h2>
<p class="services-text">Lorem Ipsum is simply dummy text of the printing and typesetting industry. Lorem Ipsum has been the industry's standard dummy text ever since the 1500s, when an unknown printer took a galley of type and</p>
<div class="btn btn-gold" style="left:110px;top:1713px;width:170px;height:47px">Read more</div>

<div class="card" style="left:463px;top:1410px;width:347px;height:366px">
  <div class="img" style="height:208px;background:linear-gradient(180deg,#5f8fc4 0%,#d9a25a 55%,#7a5a40 100%)" role="img" aria-label="Container port with cranes and a truck at sunset"></div>
  <h3 style="top:225px">Lorem Ipsum is simply</h3>
  <p style="top:259px">Lorem Ipsum is simply dummy text of the printing and typesetting industry. Lorem</p>
  <div class="more" style="top:324px">READ MORE <svg width="16" height="10" viewBox="0 0 16 10"><path d="M0 5h14M10 1l4 4-4 4" fill="none" stroke="#9d1823" stroke-width="1.6"/></svg></div>
</div>
<div class="card" style="left:828px;top:1410px;width:348px;height:366px">
  <div class="img" style="height:208px;background:linear-gradient(180deg,#aebfce 0%,#d2d8dc 45%,#6b6e70 100%)" role="img" aria-label="White truck driving on an open highway"></div>
  <h3 style="top:225px">Lorem Ipsum is simply</h3>
  <p style="top:259px">Lorem Ipsum is simply dummy text of the printing and typesetting industry. Lorem</p>
  <div class="more" style="top:320px">READ MORE <svg width="16" height="10" viewBox="0 0 16 10"><path d="M0 5h14M10 1l4 4-4 4" fill="none" stroke="#9d1823" stroke-width="1.6"/></svg></div>
</div>
<div class="dot" style="left:470px;width:43px;background:var(--gold-light)"></div>
<div class="dot" style="left:530px;width:44px"></div>
<div class="dot" style="left:588px;width:43px"></div>

<!-- blog -->
<h2 class="section-title blog-title">Our blog</h2>

<div class="card blog-card" style="left:106px;top:2118px;width:304px;height:383px">
  <div class="img" style="left:10px;right:10px;top:10px;height:207px;background:linear-gradient(180deg,#6f9ccc 0%,#c9d7e2 45%,#5a5f68 100%)" role="img" aria-label="Two trucks on a motorway"></div>
  <h3 style="top:232px">Lorem Ipsum is simply dummy</h3>
  <div class="date" style="top:304px"><svg width="14" height="14" viewBox="0 0 14 14"><rect x="1" y="2" width="12" height="11" rx="1.5" fill="none" stroke="#9d1823" stroke-width="1.3"/><path d="M1 5.5h12M4 0.5v3M10 0.5v3" stroke="#9d1823" stroke-width="1.3"/></svg>Feb 26, 2024</div>
  <div class="more" style="top:340px">READ MORE <svg width="16" height="10" viewBox="0 0 16 10"><path d="M0 5h14M10 1l4 4-4 4" fill="none" stroke="#e3e3e3" stroke-width="1.6"/></svg></div>
</div>
<div class="card blog-card" style="left:440px;top:2118px;width:304px;height:383px">
  <div class="img" style="left:10px;right:10px;top:10px;height:207px;background:linear-gradient(180deg,#aebfce 0%,#d2d8dc 45%,#6b6e70 100%)" role="img" aria-label="White truck on an open highway"></div>
  <h3 style="top:232px">Lorem Ipsum is simply dummy</h3>
  <div class="date" style="top:304px"><svg width="14" height="14" viewBox="0 0 14 14"><rect x="1" y="2" width="12" height="11" rx="1.5" fill="none" stroke="#9d1823" stroke-width="1.3"/><path d="M1 5.5h12M4 0.5v3M10 0.5v3" stroke="#9d1823" stroke-width="1.3"/></svg>Feb 26, 2024</div>
  <div class="more" style="top:340px">READ MORE <svg width="16" height="10" viewBox="0 0 16 10"><path d="M0 5h14M10 1l4 4-4 4" fill="none" stroke="#e3e3e3" stroke-width="1.6"/></svg></div>
</div>
<div class="card blog-card" style="left:774px;top:2118px;width:304px;height:383px">
  <div class="img" style="left:10px;right:10px;top:10px;height:207px;background:linear-gradient(180deg,#7f97b3 0%,#c5ced6 45%,#4f5358 100%)" role="img" aria-label="White truck with a grey trailer on a road"></div>
  <h3 style="top:232px">Lorem Ipsum is simply dummy</h3>
  <div class="date" style="top:304px"><svg width="14" height="14" viewBox="0 0 14 14"><rect x="1" y="2" width="12" height="11" rx="1.5" fill="none" stroke="#9d1823" stroke-width="1.3"/><path d="M1 5.5h12M4 0.5v3M10 0.5v3" stroke="#9d1823" stroke-width="1.3"/></svg>Feb 26, 2024</div>
  <div class="more" style="top:340px">READ MORE <svg width="16" height="10" viewBox="0 0 16 10"><path d="M0 5h14M10 1l4 4-4 4" fill="none" stroke="#e3e3e3" stroke-width="1.6"/></svg></div>
</div>
<div class="btn btn-ruby" style="left:510px;top:2556px;width:172px;height:47px">Read more</div>

<!-- contact -->
<div class="photo contact-photo" role="img" aria-label="Smiling customer support agent with a headset at a desk in an office"></div>
<svg class="contact-panel" width="770" height="722">
  <defs><linearGradient id="panelGrad" x1="0" y1="0" x2="1" y2="1"><stop offset="0" stop-color="#b42c36"/><stop offset="1" stop-color="#8b141e"/></linearGradient></defs>
  <polygon points="0,0 608,0 765,362 617,722 0,722" fill="url(#panelGrad)"/>
</svg>
<h2 class="contact-title">CONTACT US</h2>
<div class="label" style="left:127px;top:2880px">Name</div>
<div class="label" style="left:392px;top:2880px">Contact Number</div>
<div class="field" style="left:108px;top:2909px;width:259px"><svg width="14" height="14" viewBox="0 0 14 14"><circle cx="7" cy="4" r="3" fill="#fff"/><path d="M1 14a6 6 0 0112 0z" fill="#fff"/></svg></div>
<div class="field" style="left:376px;top:2909px;width:259px"><svg width="14" height="14" viewBox="0 0 24 24"><path d="M6.6 10.8a15 15 0 006.6 6.6l2.2-2.2a1 1 0 011-.25 11.4 11.4 0 003.6.6 1 1 0 011 1V20a1 1 0 01-1 1A17 17 0 013 4a1 1 0 011-1h3.5a1 1 0 011 1c0 1.25.2 2.45.6 3.6a1 1 0 01-.25 1z" fill="#fff"/></svg></div>
<div class="label" style="left:127px;top:2974px">Mail Address</div>
<div class="label" style="left:392px;top:2974px">Location</div>
<div class="field" style="left:108px;top:3005px;width:259px"><svg width="14" height="11" viewBox="0 0 14 11"><rect x="1" y="1" width="12" height="9" fill="#fff"/><path d="M1 1l6 5 6-5" fill="none" stroke="#7d121b" stroke-width="1.3"/></svg></div>
<div class="field" style="left:376px;top:3005px;width:259px"><svg width="13" height="17" viewBox="0 0 13 17"><path d="M6.5 1a5.5 5.5 0 00-5.5 5.5C1 10.5 6.5 16 6.5 16S12 10.5 12 6.5A5.5 5.5 0 006.5 1z" fill="none" stroke="#fff" stroke-width="1.8"/><circle cx="6.5" cy="6.5" r="2" fill="#fff"/></svg></div>
<div class="label" style="left:127px;top:3073px">Your Message</div>
<div class="field" style="left:108px;top:3104px;width:527px;height:122px;border-radius:16px;align-items:flex-start;padding-top:14px"><svg width="15" height="14" viewBox="0 0 15 14"><path d="M7.5 1C3.9 1 1 3.4 1 6.3c0 1.5.8 2.9 2 3.8L2.5 13l3.3-1.7c.5.1 1.1.2 1.7.2 3.6 0 6.5-2.4 6.5-5.3S11.1 1 7.5 1z" fill="#fff"/></svg></div>
<div class="btn btn-gold" style="left:110px;top:3264px;width:180px;height:47px;font-weight:600;font-size:15px">Enquiry now</div>

<!-- why choose -->
<h2 class="section-title why-title">Why choose us</h2>
<svg class="abs" style="left:0;top:3580px" width="1200" height="240">
  <g fill="none" stroke="#555" stroke-width="1.5" stroke-dasharray="7 6">
    <path d="M108 40 C140 40 160 50 170 60"/>
    <path d="M280 120 C310 160 350 175 400 190"/>
    <path d="M530 165 C570 140 600 120 640 100"/>
    <path d="M780 120 C820 150 850 170 890 175"/>
    <path d="M1020 180 C1060 175 1090 160 1105 145"/>
  </g>
</svg>
<div class="why-icon" style="left:149px;top:3588px"><span><svg width="66" height="66" viewBox="0 0 66 66" fill="none" stroke="#fff" stroke-width="2.2"><rect x="10" y="10" width="34" height="44" rx="2"/><path d="M20 6h14v8H20z"/><path d="M16 24h12M16 32h10M16 40h8"/><circle cx="46" cy="44" r="10"/><circle cx="46" cy="44" r="4"/><path d="M46 44l12-14"/></svg></span></div>
<div class="why-icon" style="left:390px;top:3686px"><span><svg width="66" height="66" viewBox="0 0 66 66" fill="none" stroke="#fff" stroke-width="2.2"><rect x="8" y="16" width="42" height="30" rx="2"/><path d="M22 54h14M29 46v8"/><path d="M44 26l10-5 10 5v12l-10 5-10-5z"/><path d="M44 26l10 5 10-5M54 31v12"/><path d="M16 10l8-4 8 4v8l-8 4-8-4z"/></svg></span></div>
<div class="why-icon" style="left:634px;top:3588px"><span><svg width="66" height="66" viewBox="0 0 66 66" fill="none" stroke="#fff" stroke-width="2.2"><circle cx="33" cy="18" r="7"/><path d="M22 40a11 11 0 0122 0"/><circle cx="14" cy="34" r="5"/><circle cx="52" cy="34" r="5"/><path d="M5 52a9 9 0 0118 0M43 52a9 9 0 0118 0"/><path d="M33 6v-3M20 10l-2-2M46 10l2-2"/></svg></span></div>
<div class="why-icon" style="left:879px;top:3686px"><span><svg width="66" height="66" viewBox="0 0 66 66" fill="none" stroke="#fff" stroke-width="2.2"><path d="M33 8l8 4v9l-8 4-8-4v-9z"/><path d="M16 36l8 4v9l-8 4-8-4v-9z"/><path d="M50 36l8 4v9l-8 4-8-4v-9z"/><path d="M22 16a18 18 0 00-8 14M44 16a18 18 0 018 14M24 58a18 18 0 0018 0"/></svg></span></div>

<div class="why-item" style="left:103px;top:3767px"><h4>Strategic Planning</h4><p>Lorem Ipsum is simply dummy text of the printing and typesetting</p></div>
<div class="why-item" style="left:344px;top:3854px"><h4>Digitalization</h4><p>Lorem Ipsum is simply dummy text of the printing and typesetting</p></div>
<div class="why-item" style="left:588px;top:3769px"><h4>Community<br>Building</h4><p>Lorem Ipsum is simply dummy text of the printing and typesetting</p></div>
<div class="why-item" style="left:834px;top:3851px"><h4>Sustainability</h4><p>Lorem Ipsum is simply dummy text of the printing and typesetting</p></div>

<!-- footer -->
<footer class="footer">
  <div class="footer-logo">Garvel Pryce<br>Transport</div>
  <span class="social" style="left:124px" aria-label="Social link"></span>
  <span class="social" style="left:166px" aria-label="Social link"></span>
  <span class="social" style="left:209px" aria-label="Social link"></span>

  <h5 style="left:407px">Page Links</h5>
  <ul style="left:410px">
    <li>Home</li><li>About Us</li><li>Services</li><li>Contact Us</li>
  </ul>

  <h5 style="left:631px">Contact Details</h5>
  <ul style="left:631px">
    <li><svg width="12" height="12" viewBox="0 0 24 24"><path d="M6.6 10.8a15 15 0 006.6 6.6l2.2-2.2a1 1 0 011-.25 11.4 11.4 0 003.6.6 1 1 0 011 1V20a1 1 0 01-1 1A17 17 0 013 4a1 1 0 011-1h3.5a1 1 0 011 1c0 1.25.2 2.45.6 3.6a1 1 0 01-.25 1z" fill="#fff"/></svg>+1 555 010 2040</li>
    <li><svg width="13" height="10" viewBox="0 0 14 11"><rect x="1" y="1" width="12" height="9" fill="#fff"/><path d="M1 1l6 5 6-5" fill="none" stroke="#0d0d0d" stroke-width="1.3"/></svg>info@garvelpryce.com</li>
    <li><svg width="11" height="14" viewBox="0 0 13 17"><path d="M6.5 1a5.5 5.5 0 00-5.5 5.5C1 10.5 6.5 16 6.5 16S12 10.5 12 6.5A5.5 5.5 0 006.5 1z" fill="#fff"/><circle cx="6.5" cy="6.5" r="2" fill="#0d0d0d"/></svg>lorem ipsum lorem</li>
    <li style="padding-left:19px">ipsum lorem ipsum</li>
  </ul>

  <div class="subscribe">
    <h6>Subscribe</h6>
    <p>Are you interested in following us for Getting Business Update</p>
    <div class="sub-input">Your Email Address
      <span class="sub-go"><svg width="16" height="12" viewBox="0 0 16 12"><path d="M1 6h13M9 1l5 5-5 5" fill="none" stroke="#0d0d0d" stroke-width="1.8"/></svg></span>
    </div>
  </div>

  <div class="footer-rule"></div>
  <div class="copyright">© 2024 Garvel Pryce Transport. I All Rights Reserved</div>
</footer>

</body>
</html>
```